Super elegant, crisp & clean Business card design required

We recently upgraded our branding - which is on our website - talvendoraphoto.com

I would like a simple, yet elegant, clean business card design please.

The font of my logo is Cinzel - and because of the natural colour - it's best to have this on a black background.

I would like to have the back of the business card - with simply my logo.

PLEASE DO NOT SUBMIT A COMPLICATED / UNCLEAN DESIGN

Industry/Entity Type

Business

Contact Information for Business Card

Talven Doroshko Photography

Font styles to use
Other font styles liked:
• Cinzel

Requirements
Must have
• A backpage with nothing but my logo
• Simple design - stands out
Should not have
• Colour that dont align with my logo
• Over complicated '/ non symmetrical design

```html
<!DOCTYPE html>
<html lang="en">
<head>
<meta charset="utf-8">
<title>Talven Doroshko Photography — Business Cards</title>
<link rel="stylesheet" href="https://fonts.googleapis.com/css2?family=Cinzel:wght@400&family=Cormorant+Garamond:ital,wght@0,400;1,400&display=swap">
<style>
  :root {
    --backdrop: #ebe5db;
    --card: #0e0e0e;
    --card-edge: #f4f1ec;
    --gold: #b39868;
    --gold-soft: #a88e62;
  }
  * { box-sizing: border-box; margin: 0; padding: 0; }
  html, body {
    width: 1200px;
    height: 1006px;
    overflow: hidden;
    background: var(--backdrop);
  }
  .sheet {
    width: 1200px;
    height: 1006px;
    display: flex;
    align-items: center;
    justify-content: center;
    gap: 60px;
  }
  .card {
    position: relative;
    width: 520px;
    height: 297px;
    background: var(--card);
    border-bottom: 3px solid var(--card-edge);
    color: var(--gold);
  }
  .brand {
    display: flex;
    flex-direction: column;
    align-items: center;
    font-family: "Cinzel", serif;
    font-weight: 400;
    color: var(--gold);
  }
  .brand__seal {
    width: 46px;
    height: 46px;
    border: 1px solid var(--gold);
    border-radius: 50%;
    margin-bottom: 14px;
  }
  .brand__name {
    font-size: 24px;
    letter-spacing: 0.04em;
    line-height: 1;
  }
  .brand__tagline {
    font-size: 11px;
    letter-spacing: 0.62em;
    margin-top: 8px;
    padding-left: 0.62em;
    line-height: 1;
  }
  .card--front .brand {
    position: absolute;
    left: 0; right: 0;
    top: 50%;
    transform: translateY(-50%);
  }
  .card--back .brand {
    position: absolute;
    left: 0; right: 0;
    top: 42px;
  }
  .contact {
    position: absolute;
    left: 278px;
    bottom: 34px;
    list-style: none;
    font-family: "Cormorant Garamond", serif;
    font-style: italic;
    font-size: 14px;
    color: var(--gold);
  }
  .contact__item {
    display: flex;
    align-items: center;
    gap: 12px;
    height: 22px;
  }
  .contact__icon {
    width: 13px;
    height: 13px;
    flex: none;
    fill: var(--gold-soft);
  }
</style>
</head>
<body>
<main class="sheet">
  <section class="card card--front" aria-label="Business card front">
    <div class="brand">
      <span class="brand__seal"></span>
      <span class="brand__name">TALVEN DOROSHKO</span>
      <span class="brand__tagline">PHOTOGRAPHY</span>
    </div>
  </section>

  <section class="card card--back" aria-label="Business card with contact details">
    <div class="brand">
      <span class="brand__seal"></span>
      <span class="brand__name">TALVEN DOROSHKO</span>
      <span class="brand__tagline">PHOTOGRAPHY</span>
    </div>
    <ul class="contact">
      <li class="contact__item">
        <svg class="contact__icon" viewBox="0 0 16 16" aria-hidden="true"><path d="M3.6 1.2l2.3 2.6-1.4 1.8c.9 2 2.5 3.6 4.5 4.6l1.8-1.4 2.6 2.3-1.4 2.6C6.7 13.3 2.6 9.3 1 3.9z"/></svg>
        <span>123 456 789</span>
      </li>
      <li class="contact__item">
        <svg class="contact__icon" viewBox="0 0 16 16" aria-hidden="true"><path d="M8 1a7 7 0 1 0 0 14A7 7 0 0 0 8 1zm0 1.3c.8.8 1.5 2.2 1.7 4H6.3C6.5 4.5 7.2 3.1 8 2.3zM5 6.3H2.4a5.7 5.7 0 0 1 3.5-3.6C5.4 3.7 5.1 5 5 6.3zm0 1.4c.1 1.3.4 2.6.9 3.6a5.7 5.7 0 0 1-3.5-3.6zm1.3 0h3.4c-.2 1.8-.9 3.2-1.7 4-.8-.8-1.5-2.2-1.7-4zm4.7 0h2.6a5.7 5.7 0 0 1-3.5 3.6c.5-1 .8-2.3.9-3.6zm0-1.4c-.1-1.3-.4-2.6-.9-3.6a5.7 5.7 0 0 1 3.5 3.6z"/></svg>
        <span>talvendoraphoto.com</span>
      </li>
      <li class="contact__item">
        <svg class="contact__icon" viewBox="0 0 16 16" aria-hidden="true"><path d="M1 3h14v10H1zm1.4 1.2L8 8.6l5.6-4.4zM2.2 5.6v6.2h11.6V5.6L8 10.1z"/></svg>
        <span>lorem@ipsum.com</span>
      </li>
    </ul>
  </section>
</main>
</body>
</html>
```